Aquatic View

We need a web design for a new window cleaning company name Tidewell Glass Care. We are located in Grand Cayman, Cayman Islands. We are a small company, a team of husband and wife. Our services include residencial interior and exterior window cleaning and commercial. Extra services such as ceiling fans cleaning, mirrors, high dusting. Home cleaning services. Power washing. Explaining the service. We want a modern, beachy style with aquatic colors. We want to use our domain name "tidewellglasscare.ky". We want to portray a clean, modern and professional design.

Target Market(s)

Big Home owners

Industry/Entity Type

Cleaning Service

Contact Information for Business Card

Company Name: Tidewell Glass Care
Name: Desmond Farrowby owner/manager
Phone: 345-9170452
Email: desmond@tidewellglasscare.ky
Website: tidewellglasscare.ky
Address: P.O.Box 2486 GT, George Town, Grand Cayman KY1-1203 Cayman Islands

Number of Pages Required

2 page

Font styles to use
Sans Serif

Colors
0592cd
0455a3
33a6d7
85cae6
cadf82
abd036
fbf289

Requirements
Nice to have
• Pictures of an ocean view and palm trees from clear windows.
• https://quorvantel.com/bidlinker/
• Use the above for "free estimate".

```html
<!DOCTYPE html>
<html lang="en">
<head>
<meta charset="utf-8">
<title>Tidewell Glass Care</title>
<link rel="stylesheet" href="https://fonts.googleapis.com/css2?family=Lato:wght@400;700&family=Open+Sans:wght@600;700&family=Poppins:wght@500;600&display=swap">
<style>
:root{
  --blue:#0592cd;
  --navy:#0455a3;
  --sky:#33a6d7;
  --ink:#2b2b2b;
  --text:#3a3a3a;
  --rule:#cfcfcf;
  --field:#f1f1f1;
  --foot:#ececec;
}
*{box-sizing:border-box;margin:0;padding:0}
html,body{width:966px;height:1200px;overflow:hidden;background:#fff}
body{position:relative;font-family:"Lato",sans-serif;color:var(--text)}
.abs{position:absolute}

.topband{left:0;top:0;width:966px;height:32px;background:linear-gradient(180deg,var(--navy),var(--blue))}
.header{left:0;top:32px;width:966px;height:48px;background:#fff}
.brand{left:90px;top:45px;display:flex;align-items:center;gap:8px;font-family:"Open Sans",sans-serif;font-weight:700;font-size:17px;line-height:22px;color:var(--navy)}
.brand .dot{width:18px;height:18px;border-radius:50%;background:var(--blue)}
.nav{left:574px;top:43px;display:flex;font-family:"Open Sans",sans-serif;font-weight:700;font-size:12.5px}
.nav a{display:block;height:27px;line-height:27px;padding:0 9px;color:var(--navy);text-decoration:none;margin-right:14px}
.nav a.active{background:var(--blue);color:#fff}

.hero{left:0;top:80px;width:966px;height:424px;
  background:
    radial-gradient(ellipse 260px 120px at 380px 60px,rgba(255,236,190,.75),rgba(255,236,190,0)),
    radial-gradient(ellipse 230px 110px at 760px 70px,rgba(255,230,180,.7),rgba(255,230,180,0)),
    radial-gradient(ellipse 200px 260px at 800px 230px,rgba(190,190,185,.55),rgba(190,190,185,0)),
    radial-gradient(ellipse 360px 120px at 480px 330px,rgba(196,130,60,.65),rgba(196,130,60,0)),
    linear-gradient(180deg,#f1e3c2 0%,#e6cfa3 30%,#cda171 55%,#a8703e 75%,#f0e6d4 100%)}
.hero-words{font-family:"Poppins",sans-serif;font-weight:600;font-size:35px;letter-spacing:-.8px;color:#fff;text-shadow:0 0 2px #333,2px 2px 3px rgba(0,0,0,.6)}
.arrow{width:28px;height:28px;border-radius:50%;background:#fff;box-shadow:0 1px 3px rgba(0,0,0,.5)}
.caption{left:0;top:458px;width:966px;height:46px;background:rgba(50,45,40,.78);color:#fff;text-align:center;line-height:46px;font-family:"Poppins",sans-serif;font-weight:600;font-size:23px;letter-spacing:.2px}

.welcome{left:80px;top:536px;font-family:"Poppins",sans-serif;font-weight:600;font-size:25px;color:var(--ink)}
.welcome span,.services-title span{color:var(--navy)}
.rule-welcome{left:80px;top:582px;width:510px;height:1px;background:var(--rule)}
.lead{left:81px;top:594px;font-weight:700;font-size:14.5px;color:var(--ink)}
.lead span{color:var(--navy)}
.intro{left:81px;top:627px;width:512px;font-size:12.4px;line-height:19.6px}
.btn{background:var(--blue);color:#fff;text-align:center;font-weight:700}
.read-more{left:80px;top:738px;width:83px;height:27px;line-height:27px;font-size:11px}

.inquiry{left:611px;top:555px;width:275px;height:218px;border:1px solid var(--rule)}
.tab-fold{top:544px;width:0;height:0;border-bottom:11px solid var(--navy)}
.tab{left:669px;top:544px;width:181px;height:34px;line-height:34px;background:var(--blue);color:#fff;text-align:center;font-family:"Open Sans",sans-serif;font-weight:700;font-size:14px}
.field{left:630px;width:243px;height:27px;background:linear-gradient(#fafafa,var(--field));border:1px solid #c9c9c9;border-radius:2px;font-size:11px;color:#222;padding:6px 6px}
.field i{font-style:normal;color:#d22}
.submit{left:631px;top:738px;width:89px;height:27px;line-height:27px;font-weight:400;font-size:12.5px}

.services-title{left:0;top:812px;width:966px;text-align:center;font-family:"Poppins",sans-serif;font-weight:600;font-size:26px;color:var(--ink)}
.rule-services{left:189px;top:862px;width:587px;height:1px;background:var(--rule)}
.rule-mark{left:476px;top:856px;width:12px;height:12px;border-radius:50%;background:#fff;border:1px solid #777}
.services-intro{left:0;top:879px;width:966px;text-align:center;font-size:15px;color:#333}
.card{top:919px;width:245px;height:169px}
.card .photo{height:134px}
.card .label{height:35px;line-height:35px;padding-left:10px;background:var(--blue);color:#fff;font-family:"Poppins",sans-serif;font-weight:600;font-size:16.5px}
.photo.residential{background:
  radial-gradient(ellipse 60px 90px at 40px 80px,rgba(40,50,120,.55),rgba(40,50,120,0)),
  radial-gradient(ellipse 50px 60px at 40px 125px,rgba(80,140,60,.6),rgba(80,140,60,0)),
  radial-gradient(ellipse 70px 50px at 175px 90px,rgba(150,90,55,.55),rgba(150,90,55,0)),
  linear-gradient(100deg,#e9eef0 0%,#cfd6da 45%,#d8d4cc 70%,#b9b2a6 100%)}
.photo.commercial{background:
  radial-gradient(ellipse 80px 40px at 60px 70px,rgba(170,110,60,.6),rgba(170,110,60,0)),
  radial-gradient(ellipse 40px 30px at 150px 110px,rgba(235,180,30,.7),rgba(235,180,30,0)),
  radial-gradient(ellipse 120px 50px at 150px 20px,rgba(255,255,255,.8),rgba(255,255,255,0)),
  linear-gradient(180deg,#dcd6cf 0%,#cbb8a2 45%,#d9d2c6 70%,#c8c0b4 100%)}
.photo.extra{background:
  radial-gradient(ellipse 30px 40px at 55px 100px,rgba(230,110,30,.7),rgba(230,110,30,0)),
  linear-gradient(90deg,#4a4c4f 0%,#6e7378 15%,#c5ccd0 35%,#e9eef1 60%,#dfe5e8 100%)}

.footer{left:0;top:1127px;width:966px;height:73px;background:var(--foot);border-top:2px solid var(--blue)}
.footer-links{left:77px;top:1154px;font-size:11.5px;color:#333;word-spacing:2px}
.footer-links b{font-weight:400;margin:0 8px}
.footer-brand{left:0;top:1153px;width:966px;text-align:center;font-family:"Open Sans",sans-serif;font-weight:700;font-size:13px;color:#555}
.copyright{right:85px;top:1155px;font-size:11px;color:#333}
</style>
</head>
<body>
<div class="abs topband"></div>
<header class="abs header"></header>
<div class="abs brand"><span class="dot"></span>Tidewell Glass Care</div>
<nav class="abs nav">
  <a class="active" href="#">HOME</a><a href="#">ABOUT</a><a href="#">SERVICES</a><a href="#">CONTACT</a>
</nav>

<div class="abs hero" role="img" aria-label="Bright residential kitchen with cream cabinets, chandeliers and an island counter"></div>
<div class="abs hero-words" style="left:16px;top:104px">Trusted</div>
<div class="abs hero-words" style="left:72px;top:160px">Reliable</div>
<div class="abs hero-words" style="left:124px;top:218px">Recommended!</div>
<div class="abs arrow" style="left:27px;top:289px">
  <svg width="28" height="28" viewBox="0 0 28 28"><path d="M16 9l-5 5 5 5" fill="none" stroke="#333" stroke-width="2.5"/></svg>
</div>
<div class="abs arrow" style="left:909px;top:289px">
  <svg width="28" height="28" viewBox="0 0 28 28"><path d="M12 9l5 5-5 5" fill="none" stroke="#333" stroke-width="2.5"/></svg>
</div>
<div class="abs caption">WE ARE RESIDENTIAL, COMMERCIAL CLEANING SERVICE FIRM</div>

<h1 class="abs welcome">Welcome To <span>Tidewell Glass Care</span></h1>
<div class="abs rule-welcome"></div>
<p class="abs lead"><span>Tidewell Glass Care</span> dolor sit amet, consectetuer adipiscing elit, sed dia</p>
<p class="abs intro">Lorem ipsum dolor sit amet, consectetuer adipiscing elit, sed diam nonummy nibh euismod tincidunt ut laoreet dolore magna aliquam erat volutpat. Ut wisi enim ad minim veniam, quis nostrud exerci tation ullamcorper suscipit lobortis nisl ut aliquip ex ea commodo consequat. Duis autem vel eum iriure dolor in hendrerit in vulputate velit.</p>
<div class="abs btn read-more">READ MORE</div>

<div class="abs inquiry"></div>
<div class="abs tab-fold" style="left:661px;border-left:8px solid transparent"></div>
<div class="abs tab-fold" style="left:850px;border-right:8px solid transparent"></div>
<div class="abs tab">QUICK INQUIRY</div>
<div class="abs field" style="top:588px">First Name <i>*</i></div>
<div class="abs field" style="top:621px">Last Name <i>*</i></div>
<div class="abs field" style="top:654px">Email <i>*</i></div>
<div class="abs field" style="top:687px;height:45px">Address<i>*</i></div>
<div class="abs btn submit">SUBMIT</div>

<h2 class="abs services-title">Our <span>Services</span></h2>
<div class="abs rule-services"></div>
<div class="abs rule-mark"></div>
<p class="abs services-intro">Lorem ipsum dolor sit amet, consectetuer adipiscing elit, sed diam nonummy nibh euismod tincidunt ut</p>

<div class="abs card" style="left:79px">
  <div class="photo residential" role="img" aria-label="Cleaners in blue overalls washing windows in a home kitchen"></div>
  <div class="label">Residential</div>
</div>
<div class="abs card" style="left:360px">
  <div class="photo commercial" role="img" aria-label="Staff mopping a tiled office lobby floor with caution signs"></div>
  <div class="label">Commercial</div>
</div>
<div class="abs card" style="left:642px">
  <div class="photo extra" role="img" aria-label="Worker in orange cleaning tall glass panes with a pole"></div>
  <div class="label">Extra Services</div>
</div>

<footer class="abs footer"></footer>
<div class="abs footer-links">HOME<b>|</b>ABOUT<b>|</b>SERVICES<b>|</b>CONTACT</div>
<div class="abs footer-brand">Tidewell Glass Care</div>
<div class="abs copyright">© 2015&nbsp; Tidewell Glass Care .&nbsp; All Rights Reserved</div>
</body>
</html>
```